Wordpress Design Project for Toy Blog

I need a Wordpress design for an upcoming blog, “Lantern Hour Notes”. The blog will provide light coverage and observations about new toy products, and examine how kids interact with different toys. I’m looking for a design that elegantly exhibits a sense of playfulness, to reflect the fact that this blog examines a fun subject - albeit in a thoughtful manner.

The background should be light, but the design should incorporate elements of color, preferably through graphics depicting toys throughout the page and/or in the logo. No depictions of copyrighted toys (Lorrettes, etc) should be used – instead, you can depict generic toys such as teddy bears, rocking horses, building blocks, etc. Overall, I do not want the blog to look loud, jarring or crowded, but it should be pleasant to look at and easy to read.

The logo should read “Lantern Hour Notes” and have some color (not just black/white/gray). The page should also have a sub-heading that reads, “a playful look at playtime and playthings”.

Reason: I've extended the deadline for 3 days as I got some later designers who expressed interest in sending submissions.

Target Market(s)

Parents, professionals that work with children, members of the toy industry.

Industry/Entity Type

Building

Requirements
Must have
• Clean design but a fun, light feel. Incorporation of primary colors and graphics evocative of children’s toys.
Should not have
• Large buttons. Graphics with obvious gradients. Clip art. Comic Sans or Courier New fonts. Brightly-colored, jarring background colors.

```html
<!DOCTYPE html>
<html lang="en">
<head>
<meta charset="utf-8">
<title>Lantern Hour Notes</title>
<link rel="stylesheet" href="https://fonts.googleapis.com/css2?family=Amatic+SC:wght@700&family=Gochi+Hand&family=Open+Sans:ital,wght@0,400;0,700;1,400;1,700&display=swap">
<style>
:root{
  --sky:#6cc3de;
  --slate:#3f6e83;
  --slate-deep:#386478;
  --paper:#ffffff;
  --frame:#dcdcdc;
  --red:#d9391c;
  --ink:#222222;
  --muted:#a9c6d2;
  --green:#1f9a2e;
  --grey-btn:#cfcfcf;
  --date-bg:#efefef;
}
*{box-sizing:border-box;margin:0;padding:0}
html,body{width:783px;height:1200px;overflow:hidden}
body{position:relative;background:var(--paper);font-family:"Open Sans",Arial,sans-serif;color:var(--ink)}
.abs{position:absolute}
.side-band{position:absolute;top:232px;width:70px;height:968px;background:linear-gradient(var(--sky) 0%,var(--sky) 10%,#5fa9c4 60%,var(--slate) 100%)}
.side-band.left{left:0}
.side-band.right{right:0}
.side-ornament{position:absolute;width:64px;height:110px;background:var(--sky);border-radius:4px}
.footer-band{position:absolute;left:0;top:1063px;width:783px;height:137px;background:var(--slate)}
.frame{position:absolute;left:59px;top:115px;width:665px;height:950px;border:7px solid var(--frame);border-bottom:none}
.panel{position:absolute;left:66px;top:120px;width:652px;height:943px;background:var(--paper)}
.brand-name{position:absolute;font-family:"Amatic SC",sans-serif;font-weight:700;color:#48b3d6}
.brand-dot{position:absolute;border-radius:50%;background:#6cc3de}
.tagline{position:absolute;font-family:"Gochi Hand",cursive;color:var(--red);font-size:15px}
.main-nav{position:absolute;left:300px;top:240px;display:flex;align-items:flex-end;font-family:"Amatic SC",sans-serif;font-weight:700;color:var(--red);font-size:26px}
.main-nav .item{display:flex;flex-direction:column;align-items:center;line-height:1}
.main-nav .sep{width:1px;height:16px;background:var(--red);margin:0 12px 5px}
.post-date{position:absolute;width:26px;height:43px;text-align:center}
.post-date .day{height:30px;background:var(--date-bg);color:var(--red);font-family:"Amatic SC",sans-serif;font-weight:700;font-size:26px;line-height:30px}
.post-date .mon{height:13px;background:var(--red);color:#fff;font-size:8px;line-height:13px}
.post-title{position:absolute;font-family:"Amatic SC",sans-serif;font-weight:700;color:var(--red);font-size:24px;line-height:1;letter-spacing:.3px}
.post-meta{position:absolute;font-size:7.5px}
.post-meta b{font-style:italic;margin-left:2px}
.post-meta b + b{margin-left:8px}
.post-photo{position:absolute;left:101px;top:377px;width:449px;height:336px;background:radial-gradient(ellipse at 48% 48%,#c9a07a 0%,#a4562e 32%,#4d4d4f 55%,#2f3032 100%)}
.post-body{position:absolute;font-size:8.2px;line-height:12.4px;width:452px}
.read-on{text-decoration:underline;display:inline-block}
.read-more{position:absolute;left:283px;top:1030px;width:69px;height:22px;background:var(--grey-btn);color:#fff;border-radius:3px;font-size:8.5px;line-height:22px;text-align:center}
.search-box{position:absolute;left:590px;top:307px;width:112px;height:21px;border:1.2px solid #333;border-radius:6px}
.widget-label{position:absolute;font-family:"Gochi Hand",cursive;font-size:13.5px;color:#333}
.cat-list{position:absolute;right:85px;top:386px;list-style:none;text-align:right;font-size:9.4px;font-weight:700;font-style:italic;line-height:20.7px}
.mail-input{position:absolute;left:590px;top:559px;width:117px;height:22px;border:1.2px solid #333;border-radius:8px}
.submit-btn{position:absolute;left:671px;top:587px;width:32px;height:21px;background:var(--green);color:#fff;font-family:"Gochi Hand",cursive;font-size:11px;text-align:center;line-height:21px}
.ad{position:absolute;width:46px;height:46px}
.meta-list{position:absolute;right:85px;top:842px;list-style:none;text-align:right;font-size:8.6px;line-height:14px}
.footer-col{position:absolute;color:var(--muted);font-size:8.6px;line-height:14px;list-style:none}
</style>
</head>
<body>
  <div class="side-band left"></div>
  <div class="side-band right"></div>
  <div class="side-ornament" style="left:0;top:125px" role="img" aria-label="Scattered blue block shapes"></div>
  <div class="side-ornament" style="right:0;top:125px" role="img" aria-label="Scattered blue block shapes"></div>
  <div class="side-ornament" style="left:0;top:890px;background:#5a9fba" role="img" aria-label="Scattered blue block shapes"></div>
  <div class="side-ornament" style="right:0;top:890px;background:#5a9fba" role="img" aria-label="Scattered blue block shapes"></div>
  <div class="footer-band"></div>

  <div class="frame"></div>
  <div class="panel"></div>

  <!-- header -->
  <div class="brand-dot" style="left:338px;top:70px;width:124px;height:124px" role="img" aria-label="Blog brand mark"></div>
  <div class="brand-name" style="left:382px;top:30px;font-size:24px">Lantern Hour Notes</div>
  <div class="tagline" style="left:224px;top:148px">a playful look at</div>
  <div class="tagline" style="left:482px;top:148px">playtime + playthings</div>

  <nav class="main-nav">
    <div class="item"><svg width="8" height="11" viewBox="0 0 8 11"><path d="M1.5 3a2.5 2.5 0 1 1 3.5 2.3c-.8.4-1 .9-1 1.7" fill="none" stroke="#d9391c" stroke-width="1.6"/><circle cx="4" cy="9.6" r="1" fill="#d9391c"/></svg><span>About</span></div>
    <div class="sep"></div>
    <div class="item"><svg width="13" height="12" viewBox="0 0 13 12"><path d="M6.5 0 13 6h-2v6H2V6H0z" fill="#d9391c"/></svg><span>Home</span></div>
    <div class="sep"></div>
    <div class="item" style="align-items:flex-end"><svg width="12" height="12" viewBox="0 0 12 12" style="margin-right:14px"><path d="M9 0 12 3 4 11 0 12 1 8z" fill="#d9391c"/></svg><span>Contact</span></div>
  </nav>

  <!-- post one -->
  <div class="post-date" style="left:106px;top:310px"><div class="day">5</div><div class="mon">FEB</div></div>
  <h2 class="post-title" style="left:147px;top:310px">Hazel Wren | Beautiful, Eco-Friendly Wooden Toys</h2>
  <div class="post-meta" style="left:146px;top:336px">This entry was posted in <b>Educational Toys</b><b>Leave A Comment</b></div>
  <div class="post-photo" role="img" aria-label="Carved wooden bowl filled with painted wooden acorns on a woven mat"></div>
  <p class="post-body" style="left:103px;top:722px">One of the gifts I love most from this past holiday season was this set of wooden counting acorns by Hazel Wren.<br>&nbsp;Gorgeously painted and charmingly simple, they evoke a time when toy makers carved simple figurines out of<br>wood, and children used their imaginations to take those figurines and create new worlds in their minds.<br>Hazel Wren’s toys and products are designed for babies, toddlers and pre-schoolers.&nbsp; The best thing about them<br>for parents, though, is that they’re so beautiful they can be used for decoration, which is how I use my acorns!<br>&nbsp;After your child is done playing with them, simply slip them into a glass vase or even a cup.&nbsp; So lovely!<br><span class="read-on">Read On...</span></p>

  <!-- post two -->
  <div class="post-date" style="left:101px;top:834px"><div class="day">1</div><div class="mon">FEB</div></div>
  <h2 class="post-title" style="left:140px;top:834px">Kitebox Toys &nbsp;Reelhouse for Toys!</h2>
  <div class="post-meta" style="left:139px;top:861px">This entry was posted in <b>Uncategorized</b><b>Leave A Comment</b></div>
  <p class="post-body" style="left:101px;top:890px">Have you ever heard of Kitebox Toys? It’s like Reelhouse for toys – only the toys are tailored to your child’s age and<br>developmental level. Here’s what you do:<br>1. Tell them about your child via a survey<br>2.&nbsp; Kitebox Toys sends you a box of four fun, innovation and educational toys that help your child develop<br>cognitive, language, motor and other skills, as well as helpful play ideas for parents!<br>3. You can keep that box for several weeks – and they don’t even charge late fees.&nbsp; And of course, free shipping!<br>4.&nbsp; When you send the box back, you’ll get another box!<br><span class="read-on">Read On...</span></p>

  <div class="read-more">Read More...</div>

  <!-- sidebar -->
  <div class="search-box">
    <svg class="abs" style="right:5px;top:3px" width="13" height="13" viewBox="0 0 13 13"><circle cx="5.5" cy="5.5" r="4.3" fill="none" stroke="#d9391c" stroke-width="1.6"/><path d="M8.6 8.6 12.3 12.3" stroke="#d9391c" stroke-width="1.8"/></svg>
  </div>
  <div class="widget-label" style="left:598px;top:340px">↰ Have a look around ↴</div>
  <ul class="cat-list">
    <li>Educational Toys</li><li>STEM</li><li>New Toys</li><li>Cool Products</li><li>Uncategorized</li><li>Services For Parents</li>
  </ul>
  <div class="widget-label" style="left:610px;top:532px">Join the mailing list ↴</div>
  <div class="mail-input"></div>
  <div class="submit-btn">Submit</div>

  <div class="ad" style="left:594px;top:640px;background:#2d8fd0"></div>
  <div class="ad" style="left:652px;top:640px;background:#f4d2dc"></div>
  <div class="ad" style="left:594px;top:691px;background:#c9202b"></div>
  <div class="ad" style="left:652px;top:691px;background:#e0565f"></div>
  <div class="ad" style="left:594px;top:745px;background:#b83a4e"></div>
  <div class="ad" style="left:652px;top:745px;background:#f4a52a"></div>

  <div class="widget-label" style="left:666px;top:814px">META ↴</div>
  <ul class="meta-list"><li>Log in</li><li>Entries RSS</li><li>Comments RSS</li><li>Blogframe.org</li></ul>

  <!-- footer -->
  <ul class="footer-col" style="left:97px;top:1084px"><li>META:</li><li>&nbsp;</li><li>&nbsp;</li><li>Log in</li><li>Entries RSS</li><li>Comments RSS</li><li>Blogframe.org</li></ul>
  <ul class="footer-col" style="left:255px;top:1087px"><li>Categories:</li><li>Educational Toys</li><li>STEM</li><li>New Toys</li><li>Cool Products</li><li>Uncategorized</li><li>Services For Parents</li></ul>
  <ul class="footer-col" style="left:414px;top:1086px"><li>Links:</li><li>&nbsp;</li><li>Home</li><li>About</li><li>Contact</li><li>Favourite Toys</li><li>Chirpline</li></ul>
  <div class="brand-dot" style="left:562px;top:1090px;width:94px;height:94px" role="img" aria-label="Blog brand mark"></div>
  <div class="brand-name" style="left:612px;top:1068px;font-size:17px">Lantern Hour Notes</div>
</body>
</html>
```